mechanical repair shop

our shop repairs light and medium duty trucks

we sell tires , do oil changes, engine and transmissions
vehicle accessories, alignments, brakes , exhaust, all major and minor repairs.
Updates

if you would like to get a hold of me email: milo.hensworth@quarrytide.net tel: 1-780-555-0148

Target Market(s)

light and medium duty trucks and cars

Industry/Entity Type

Shop

Colors
f37122

Requirements
Must have
• visual sales displays
Nice to have
• pictures

```html
<!DOCTYPE html>
<html lang="en">
<head>
<meta charset="utf-8">
<title>Quarrytide Services Ltd. – Truck Repair Flyer</title>
<link href="https://fonts.googleapis.com/css2?family=Bebas+Neue&family=Oswald:wght@300;400;500;700&family=Montserrat:ital,wght@0,400;1,400&display=swap" rel="stylesheet">
<style>
  :root {
    --orange: #f37122;
    --black: #050505;
    --white: #ffffff;
    --ink: #1a1a1a;
    --stage: #3a3a3a;
    --photo-light: #e9e9e9;
    --photo-mid: #b9b9b9;
    --photo-dark: #3b3b3b;
  }
  * { margin: 0; padding: 0; box-sizing: border-box; }
  html, body { width: 960px; height: 1200px; overflow: hidden; }
  body { background: var(--stage); position: relative; }
  .flyer {
    position: absolute; left: 56px; top: 0;
    width: 848px; height: 1200px;
    background: var(--white); overflow: hidden;
  }
  .shapes { position: absolute; inset: 0; }
  .hero-photo {
    position: absolute; left: 340px; top: 14px; width: 495px; height: 334px;
    border-radius: 18px 18px 30px 30px;
    background: linear-gradient(160deg, var(--photo-light) 0%, #f7f7f7 45%, var(--photo-mid) 100%);
  }
  .brand {
    position: absolute; left: 40px; top: 262px; width: 290px;
    text-align: center; color: var(--white);
  }
  .brand-name {
    font-family: "Oswald", sans-serif; font-weight: 700;
    font-size: 46px; line-height: 1; letter-spacing: 1px; color: var(--orange);
  }
  .brand-sub {
    margin-top: 8px;
    font-family: "Montserrat", sans-serif; font-size: 14px; color: var(--white);
  }
  .brand-tag {
    margin-top: 3px;
    font-family: "Montserrat", sans-serif; font-size: 11px; color: var(--orange);
  }
  .headline {
    position: absolute; left: 524px; top: 416px;
    font-family: "Bebas Neue", "Oswald", sans-serif; font-weight: 400;
    font-size: 43px; line-height: 45px; letter-spacing: -0.3px;
    color: var(--ink); text-transform: uppercase; white-space: nowrap;
  }
  .headline .accent { color: var(--white); }
  .section-title {
    position: absolute;
    font-family: "Oswald", sans-serif; font-weight: 500;
    font-size: 40px; letter-spacing: -1px; color: var(--ink); line-height: 1;
  }
  .services-title { left: 32px; top: 538px; }
  .about-title { left: 433px; top: 758px; }
  .service-list {
    position: absolute; left: 32px; top: 596px; list-style: none;
    font-family: "Montserrat", sans-serif; font-size: 15px; color: var(--ink);
  }
  .service-list li { height: 32.7px; display: flex; align-items: center; white-space: nowrap; }
  .service-list svg { width: 15px; height: 15px; margin-right: 11px; flex: none; }
  .work-photo {
    position: absolute; top: 615px; width: 192px; height: 128px;
  }
  .work-photo.tires { left: 436px; background: linear-gradient(135deg, #5a5a5a, var(--photo-dark) 55%, #9a2b22); }
  .work-photo.oil { left: 636px; background: linear-gradient(135deg, #c8c8c8, #7d7d7d 55%, #c89a20); }
  .about-text {
    position: absolute; left: 431px; top: 813px; width: 392px;
    font-family: "Montserrat", sans-serif; font-style: italic;
    font-size: 13.4px; line-height: 21.4px; color: var(--ink);
  }
  .website {
    position: absolute; left: 36px; top: 1144px;
    font-family: "Oswald", sans-serif; font-weight: 300;
    font-size: 23px; color: var(--white); white-space: nowrap;
  }
  .contact {
    position: absolute; right: 43px; top: 1090px; text-align: right;
    font-family: "Oswald", sans-serif; white-space: nowrap;
  }
  .contact-call { font-weight: 400; font-size: 25px; color: var(--orange); letter-spacing: -0.3px; }
  .contact-phone {
    display: flex; align-items: center; justify-content: flex-end; gap: 8px;
    font-weight: 300; font-size: 46px; line-height: 1.1; color: var(--white); letter-spacing: -0.5px;
  }
  .contact-phone svg { width: 26px; height: 40px; }
</style>
</head>
<body>
<main class="flyer">
  <svg class="shapes" viewBox="0 0 848 1200" width="848" height="1200" aria-hidden="true">
    <polygon points="0,0 848,193 848,328 0,508" fill="var(--black)"/>
    <polygon points="350,443 848,340 848,598 525,568" fill="var(--orange)"/>
    <polygon points="0,1088 282,1135 330,1200 0,1200" fill="var(--orange)"/>
    <polygon points="290,1120 728,1038 848,1084 848,1200 345,1200" fill="var(--black)"/>
  </svg>

  <div class="hero-photo" role="img" aria-label="White light-duty box truck"></div>

  <div class="brand">
    <div class="brand-name">QUARRYTIDE</div>
    <div class="brand-sub">Quarrytide Services Ltd.</div>
    <div class="brand-tag">Truck Services &amp; Maintenance</div>
  </div>

  <h1 class="headline">
    <span class="accent">Your complete</span><br>
    Light &amp; Medium Duty<br>
    <span class="accent">Truck repair facility</span>
  </h1>

  <h2 class="section-title services-title">Services We Offer:</h2>
  <svg width="0" height="0" style="position:absolute">
    <symbol id="tick" viewBox="0 0 16 16">
      <circle cx="8" cy="8" r="6.5" fill="none" stroke="#f37122" stroke-width="1.6"/>
      <path d="M4.8 8.2 L7.3 10.6 L14.5 2.8" fill="none" stroke="#f37122" stroke-width="1.8" stroke-linecap="round" stroke-linejoin="round"/>
    </symbol>
  </svg>
  <ul class="service-list">
    <li><svg><use href="#tick"/></svg>Factory recommended service</li>
    <li><svg><use href="#tick"/></svg>Oil change</li>
    <li><svg><use href="#tick"/></svg>Fuel system repair and maintenance</li>
    <li><svg><use href="#tick"/></svg>Battery system diagnosis &amp; repair</li>
    <li><svg><use href="#tick"/></svg>Check engine light</li>
    <li><svg><use href="#tick"/></svg>Electrical problems</li>
    <li><svg><use href="#tick"/></svg>Engine performance</li>
    <li><svg><use href="#tick"/></svg>Exhaust problems</li>
    <li><svg><use href="#tick"/></svg>Tires</li>
    <li><svg><use href="#tick"/></svg>30/60/90 K mileage maintenance services</li>
    <li><svg><use href="#tick"/></svg>Cooling system repair and maintenance</li>
    <li><svg><use href="#tick"/></svg>Air conditioning / heating repair</li>
    <li><svg><use href="#tick"/></svg>Brake system</li>
    <li><svg><use href="#tick"/></svg>Steering &amp; suspension</li>
  </ul>

  <div class="work-photo tires" role="img" aria-label="Mechanic mounting a tire in the shop"></div>
  <div class="work-photo oil" role="img" aria-label="Fresh oil being poured into an engine"></div>

  <h2 class="section-title about-title">About Us:</h2>
  <p class="about-text">Quarrytide Services Ltd. has set up and successfully operates a complete equipment repair facility. First set up to be a dedicated repair shop for a single large client, Quarrytide has now expanded to include all manner of clients with diverse equipment needs. With Journeyman and Apprentice HD mechanics available 24 hours a day our facility is ready to handle all of your equipment needs. We are an ‘approved’ repair facility for a growing list of equipment manufacturers including: Torvane, Halbrook, Liftera, KMR, Stratolift etc.</p>

  <div class="website">www.quarrytide.net</div>

  <div class="contact">
    <div class="contact-call">Call us for more information</div>
    <div class="contact-phone">
      <svg viewBox="0 0 26 40" aria-hidden="true"><path d="M6 2 C2 4 1 9 2 16 C3 25 8 34 14 38 C17 40 20 39 22 37 L24 34 L18 27 L14 29 C11 25 9 20 9 15 L13 12 L11 2 Z" fill="#ffffff"/></svg>
      <span>780 555 0148</span>
    </div>
  </div>
</main>
</body>
</html>
```